accomplished personal trainer, former elite gymnast from Russia, highly professional and experienced

Established Fitness trainer in California requires a new web site to attract personal clients and build her group exercise classes.

Here is an example of another fitness trainer's site that I really liked the technology:
http://www.tedvorlam.com

Below I have inserted my current web site: www.quelbornfitnesslodi.com
You can use this web site for the principal content, such as my background and qualifications.

Target Market(s)

Anyone who wants to improve their fitness levels and wellness in general. Anyone who needs directions and instruction on how to exercise. I can train anyone from elite athlete to a disabled person.

Industry/Entity Type

Fitness

Coding

Coded - Design and coding required

Number of Pages Required

5+ page

Font styles to use
Sans Serif

Requirements
Must have
• Easy to navigate main info about me, location, services, contact, benefits of using my services.
• Would be great to create unique representation of me as a trainer and a person, using new technologies and new ideas. Make it different from the other websites. Having its own character. Not too complicated and heavy with information, but an eye catching, useful and fun to navigate.
Nice to have
• new technology, easy access to information, the idea of enjoyment of life, lightness about achieving any goal, spiritual wisdom, unique design. I am planning to insert educational videos, advise, maybe jokes. Sign in, shopping cart, logo, should be easy for me to make changes in content.
Should not have
• cliché, outdated technology, too complicated,

```html
<!DOCTYPE html>
<html lang="en">
<head>
<meta charset="utf-8">
<title>Quelborn Fitness Lodi</title>
<link rel="stylesheet" href="https://fonts.googleapis.com/css2?family=Open+Sans:wght@400;600;700&family=Merriweather:ital,wght@1,400&family=Arimo:wght@400&display=swap">
<style>
:root{
  --white:#ffffff;
  --ink:#1c1c1c;
  --text:#3a3a3a;
  --muted:#8a8a8a;
  --accent:#1a8fd6;
  --form-blue:#1492d6;
  --band:#f3f3f3;
  --dark:#151515;
  --footer:#ececec;
  --bottom:#cfcfcf;
}
*{margin:0;padding:0;box-sizing:border-box}
html,body{width:1200px;height:2546px;overflow:hidden}
body{position:relative;background:var(--white);font-family:"Open Sans",sans-serif;color:var(--text)}
.abs{position:absolute}

/* Header */
.site-header{left:0;top:0;width:1200px;height:78px;background:var(--white)}
.brand{left:98px;top:27px;font-size:21px;font-weight:700;letter-spacing:1.5px;color:var(--ink)}
.nav a{position:absolute;top:32px;font-size:13px;color:var(--ink);text-decoration:none;text-transform:uppercase;white-space:nowrap}

/* Hero */
.hero{left:0;top:78px;width:1200px;height:489px;background:linear-gradient(100deg,#4e6a2c 0%,#7fa34a 35%,#a7c76a 60%,#6d9a3e 100%)}
.hero-title{left:97px;top:226px;font-size:42px;font-weight:700;color:var(--white);letter-spacing:1px}
.hero-sub{left:98px;top:293px;width:470px;font-size:14px;line-height:23px;color:var(--white)}
.btn{position:absolute;display:flex;align-items:center;justify-content:center;font-size:13px;text-transform:uppercase;text-decoration:none}
.btn-hero{left:98px;top:377px;width:133px;height:42px;border:2px solid var(--white);color:var(--white);font-weight:600}
.btn-outline{border:2px solid var(--accent);color:var(--accent);background:var(--white)}

/* Welcome */
.welcome-title{left:97px;top:622px;font-size:28px;font-weight:700;color:var(--ink)}
.welcome-lead{left:97px;top:678px;width:458px;font-size:14px;line-height:22px;color:var(--ink);text-transform:uppercase;text-align:justify}
.welcome-body{left:97px;top:738px;width:458px;font-size:11.5px;line-height:22.5px;color:var(--muted);text-align:justify}
.video-frame{left:645px;top:628px;width:455px;height:280px;border-radius:12px;background:var(--white);box-shadow:0 0 8px rgba(0,0,0,.25);padding:6px}
.video-still{width:100%;height:100%;border-radius:8px;background:linear-gradient(160deg,#2f5a23 0%,#4f7e32 55%,#7aa84c 100%);position:relative}

/* Services */
.tile{top:972px;height:236px}
.services-band{left:0;top:1208px;width:1200px;height:246px;background:var(--band)}
.service{top:1238px;width:360px;text-align:center}
.service h3{font-size:17px;font-weight:700;color:var(--ink);text-transform:uppercase}
.service p{margin-top:10px;font-size:12px;line-height:22px;color:var(--text)}

/* Testimonial */
.testimonial{left:0;top:1454px;width:1200px;height:338px;background:linear-gradient(180deg,#1b1d18 0%,#0f100e 100%)}
.quote-text{left:178px;top:1590px;width:845px;text-align:center;font-family:"Merriweather",serif;font-style:italic;font-size:13.5px;line-height:31px;color:var(--white)}
.quote-author{left:0;top:1712px;width:1200px;text-align:center;font-size:17px;font-weight:700;color:var(--white)}

/* Contact form */
.signup{left:98px;top:1853px;width:392px;height:326px;background:var(--form-blue)}
.signup label{position:absolute;left:32px;font-size:14px;color:var(--white)}
.signup .field{position:absolute;left:32px;width:329px;height:40px;background:var(--white);border-radius:3px;box-shadow:inset 0 2px 4px rgba(0,0,0,.15)}
.signup .privacy{position:absolute;left:30px;top:270px;font-size:11px;font-style:italic;color:var(--white)}
.btn-signup{left:239px;top:258px;width:122px;height:40px;border:2px solid var(--white);color:var(--white);font-weight:600;font-size:14px}

/* Tips */
.tips-title{left:577px;top:1868px;font-size:28px;font-weight:700;color:var(--ink)}
.tips-lead{left:577px;top:1920px;width:480px;font-size:14px;line-height:26px;color:var(--ink);text-transform:uppercase}
.tips-list{left:577px;top:1986px;list-style:none}
.tips-list li{height:25.5px;font-size:11.5px;color:var(--muted);padding-left:35px;position:relative}
.tips-list li::before{content:"»";position:absolute;left:2px;top:-2px;color:var(--accent);font-size:14px}

/* Footer */
.site-footer{left:0;top:2237px;width:1200px;height:249px;background:linear-gradient(90deg,#e4e4e4 0%,#f4f4f4 100%)}
.contact-block{left:107px;top:2283px;width:400px;text-align:center;font-family:"Arimo",sans-serif;color:var(--ink)}
.contact-name{font-size:17px;letter-spacing:.5px}
.contact-phone{margin-top:10px;font-size:34px}
.contact-mail{margin-top:16px;font-size:13px;line-height:26px;color:var(--text)}
.footer-col{top:2295px;font-family:"Arimo",sans-serif}
.footer-col h4{font-size:17px;font-weight:400;color:var(--ink);text-transform:uppercase;margin-bottom:14px;letter-spacing:.5px}
.footer-col a{display:block;font-size:13px;line-height:25.5px;color:var(--text);text-decoration:none}
.bottom-bar{left:0;top:2486px;width:1200px;height:60px;background:var(--bottom);text-align:center;line-height:60px;font-family:"Arimo",sans-serif;font-size:13px;color:var(--text)}
</style>
</head>
<body>

<header class="abs site-header">
  <div class="abs brand">QUELBORN FITNESS LODI</div>
  <nav class="nav">
    <a style="left:500px">Group Classes</a>
    <a style="left:640px">Personal Training</a>
    <a style="left:805px">About Quelborn</a>
    <a style="left:960px">Contact</a>
    <a style="left:1067px">Blog</a>
  </nav>
</header>

<section class="abs hero" role="img" aria-label="Group of smiling people stretching together in a sunny green park"></section>
<svg class="abs" style="left:35px;top:280px" width="26" height="86" viewBox="0 0 26 86"><polyline points="24,2 2,43 24,84" fill="none" stroke="#fff" stroke-width="2"/></svg>
<svg class="abs" style="left:1140px;top:280px" width="26" height="86" viewBox="0 0 26 86"><polyline points="2,2 24,43 2,84" fill="none" stroke="#fff" stroke-width="2"/></svg>
<h1 class="abs hero-title">FITNESS OUTDOOR</h1>
<p class="abs hero-sub">We are constantly working to raise the bar on our services. If you have any questions or concerns about your experience</p>
<a class="btn btn-hero">Join us now</a>

<section>
  <h2 class="abs welcome-title">WELCOME TO QUELBORN FITNESS</h2>
  <p class="abs welcome-lead">At vero eos et accusamus et iusto the odio dignissimos ducimus qui blanditiis praesentium</p>
  <p class="abs welcome-body">At vero eos et accusamus et iusto odio dignissimos ducimus qui blanditiis praesentium voluptatum deleniti atque corrupti quos dolores et quas molestias excepturi sint occaecati cupiditate non provident, similique sunt in culpa qui officia deserunt mollitia animi, id est laborum et dolorum fuga. Et harum quidem rerum facilis est et expedita distinctio. quos dolores et quas molestias</p>
  <a class="btn btn-outline" style="left:98px;top:872px;width:115px;height:38px">Read more</a>
  <div class="abs video-frame">
    <div class="video-still" role="img" aria-label="Trainer doing a stretching split on the grass, video preview">
      <svg style="position:absolute;left:199px;top:118px" width="50" height="50" viewBox="0 0 50 50"><circle cx="25" cy="25" r="23" fill="none" stroke="#fff" stroke-width="2.5"/><polygon points="20,15 20,35 35,25" fill="#fff"/></svg>
    </div>
  </div>
</section>

<section>
  <div class="abs tile" style="left:0;width:400px;background:linear-gradient(150deg,#5f8c3a,#9fc266)" role="img" aria-label="Outdoor group class doing squats in a park"></div>
  <div class="abs tile" style="left:400px;width:398px;background:linear-gradient(150deg,#2e4a22,#6e8f56)" role="img" aria-label="Trainer hanging from a tree branch during personal training"></div>
  <div class="abs tile" style="left:798px;width:402px;background:linear-gradient(150deg,#6f9a45,#b4cf85)" role="img" aria-label="Trainer portrait in a park"></div>
  <div class="abs services-band"></div>
  <div class="abs service" style="left:20px">
    <h3>Group Classes</h3>
    <p>Quelborn Group Exercise classes are designed people<br>of all fitness levels. Quelborn's group classes take a<br>holistic approach and make sure you work</p>
  </div>
  <a class="btn btn-outline" style="left:143px;top:1357px;width:115px;height:38px">Read more</a>
  <div class="abs service" style="left:420px">
    <h3>Personal Training</h3>
    <p>Private sessions will provide you with motivation you<br>need to reach your goals. As a nationally certified trainer,<br>Mira will make sure you're working</p>
  </div>
  <a class="btn btn-outline" style="left:542px;top:1357px;width:115px;height:38px">Read more</a>
  <div class="abs service" style="left:818px">
    <h3>About Quelborn Fitness</h3>
    <p>We are constantly working to raise the bar on our<br>services. If you have any questions or concerns about<br>your experience, please let us know.</p>
  </div>
  <a class="btn btn-outline" style="left:941px;top:1357px;width:115px;height:38px">Read more</a>
</section>

<section class="abs testimonial" role="img" aria-label="Dark background of a person training with suspension straps outdoors"></section>
<svg class="abs" style="left:577px;top:1516px" width="46" height="46" viewBox="0 0 46 46"><circle cx="23" cy="23" r="23" fill="#fff"/><path d="M13 29 q0-10 7-13 l1 3 q-4 2-4 5 h4 v6 h-8z M25 29 q0-10 7-13 l1 3 q-4 2-4 5 h4 v6 h-8z" fill="#151515"/></svg>
<p class="abs quote-text">“I have known Mira for many years as a fitness trainer and workout class instructor. She is truly one of the very best in the business. Mira is extremely knowledgeable about human physiology and teaching. Her personality is professional, informative, and caring. She would always put “her all” into each of her classes.”</p>
<p class="abs quote-author">— LENA HARWOOD</p>

<form class="abs signup">
  <label style="top:25px">Name :</label>
  <div class="field" style="top:47px"></div>
  <label style="top:105px">Phone or Email:</label>
  <div class="field" style="top:127px"></div>
  <label style="top:185px">Message:</label>
  <div class="field" style="top:207px"></div>
  <span class="privacy">We respect your privacy.</span>
  <span class="btn btn-signup">Sign up</span>
</form>

<section>
  <h2 class="abs tips-title">TIPS TO MEMBERS</h2>
  <p class="abs tips-lead">We are constantly working to raise the bar on our services. If you have any questions or concerns</p>
  <ul class="abs tips-list">
    <li>At vero eos et accusamus et iusto odio dignissimos</li>
    <li>At vero eos et accusamus et iusto odio dignissimos</li>
    <li>At vero eos et accusamus et iusto odio dignissimos</li>
    <li>At vero eos et accusamus et iusto odio dignissimos</li>
  </ul>
  <a class="btn btn-outline" style="left:577px;top:2116px;width:115px;height:39px">Read more</a>
</section>

<footer class="abs site-footer"></footer>
<div class="abs contact-block">
  <div class="contact-name">MIRA TOLVANEN</div>
  <div class="contact-phone">+1 (555) 014-7732</div>
  <div class="contact-mail">tolvanen@mailbox.net<br>Sales@quelbornfitnesslodi.com</div>
</div>
<div class="abs footer-col" style="left:582px">
  <h4>Quick Link</h4>
  <a>Team</a><a>Reviews</a><a>Blog</a><a>Contact</a>
</div>
<div class="abs footer-col" style="left:767px">
  <h4>Information</h4>
  <a>Terms and Condition</a><a>Privacy policy</a><a>Site Map</a>
</div>
<div class="abs footer-col" style="left:972px">
  <h4>Company</h4>
  <a>Why Us</a><a>Contact</a><a>Customers</a><a>Affiliates</a>
</div>
<div class="abs bottom-bar">Copyrights@2016Company Name, All rights Reseve</div>

</body>
</html>
```